Pressure Washing Hog Confinements

We clean and disinfect Hog confinements in-order to receive new pigs.

Needs to emphasis Clean Healthy barns (pigs), work done in timely manner, 100% satisfied, Bio-security rules followed. I do not have specific colors, no logo's.

Contact Information will be sent once design is agreed on.
Business Name - Brandt & Daughters Power Washing
Phone Number - Send latter
E-mail - Send latter
Web Address - Send latter

Target Market(s)

Farmers

Industry/Entity Type

Business

Requirements
Must have
• We are Insured
Bio-Security
100% Satisfied
Water Conservation

Size - 2 sided Postcard 8.5" x 5.5"
Nice to have
• I want to emphasize healthy and happy pigs because of a quality job done. Picture of pigs dose not need to be used but may be just an example.

Also attached is picture of a barn I would like to see used. on the back side. Every owner seeing this will know this is a hog barn and have an idea what we do.

```html
<!DOCTYPE html>
<html lang="en">
<head>
<meta charset="utf-8">
<title>Brandt &amp; Daughters Power Washing – Postcard</title>
<link rel="stylesheet" href="https://fonts.googleapis.com/css2?family=Crimson+Pro:wght@400&family=Open+Sans:wght@400;600;700&family=Quicksand:wght@700&display=swap">
<style>
  :root {
    --maroon: #8b3f48;
    --panel: #f1f1f3;
    --ink: #3d3d40;
    --rule: #555558;
    --white: #ffffff;
    --stage: #e6e3df;
    --sky: #4f8fd6;
    --barn: #d9dadb;
    --gravel: #e2d6c8;
  }
  * { box-sizing: border-box; margin: 0; padding: 0; }
  html, body { width: 1200px; height: 572px; overflow: hidden; }
  body { background: var(--stage); position: relative; font-family: "Open Sans", Arial, sans-serif; }

  .card {
    position: absolute; top: 103px; width: 568px; height: 366px;
    background: var(--panel); overflow: hidden;
    box-shadow: 0 2px 8px rgba(0,0,0,.25);
  }
  .card--front { left: 21px; }
  .card--back { left: 611px; background: var(--white); }

  /* Front */
  .headline-band {
    position: absolute; left: 0; top: 0; width: 100%; height: 181px;
    background: var(--maroon);
    display: flex; align-items: center; justify-content: center;
  }
  .headline {
    font-family: "Crimson Pro", Georgia, serif; font-weight: 400;
    color: var(--white); font-size: 38px; line-height: 43px;
    text-align: center; text-transform: uppercase; letter-spacing: 1.5px;
    margin-top: 4px;
  }
  .rule { position: absolute; height: 3px; }
  .rule--light { background: var(--white); }
  .rule--dark { background: var(--rule); }
  .front-rule-light { left: 73px; width: 495px; top: 172px; }
  .front-rule-dark { left: 0; width: 494px; top: 187px; }

  .service {
    position: absolute; left: 0; width: 100%; top: 206px;
    text-align: center; color: var(--ink);
    font-weight: 700; font-size: 22.5px; line-height: 32px;
  }
  .brand {
    position: absolute; left: 0; width: 100%; top: 292px;
    text-align: center; color: var(--maroon);
    font-family: "Quicksand", "Trebuchet MS", sans-serif; font-weight: 700;
    font-size: 44px; line-height: 54px; letter-spacing: 1px;
  }
  .web {
    position: absolute; left: 0; width: 100%; top: 337px;
    text-align: center; color: var(--ink); font-size: 18px; line-height: 24px;
  }

  /* Back */
  .barn-photo {
    position: absolute; left: 0; top: 0; width: 277px; height: 162px;
    background: linear-gradient(to bottom, var(--sky) 0%, #8fbbe8 45%, var(--barn) 55%, var(--barn) 72%, var(--gravel) 78%, var(--gravel) 100%);
  }
  .info-panel {
    position: absolute; left: 0; top: 162px; width: 277px; height: 204px;
    background: var(--panel);
  }
  .photo-band { position: absolute; left: 0; top: 162px; width: 277px; height: 10px; background: var(--maroon); }
  .back-rule-light { left: 36px; width: 241px; top: 174px; }
  .back-rule-dark { left: 0; width: 242px; top: 187px; }

  .insured {
    position: absolute; left: 11px; top: 197px;
    color: var(--maroon); font-size: 17.5px; line-height: 22px; font-family: Arial, "Open Sans", sans-serif;
  }
  .benefits {
    position: absolute; left: 11px; top: 222px; list-style: none;
    font-family: Arial, "Open Sans", sans-serif; color: var(--ink);
    font-size: 18.5px; line-height: 25.5px;
  }
  .benefits li { display: flex; align-items: center; gap: 5px; }
  .benefits svg { width: 15px; height: 15px; flex: none; }

  .return-address {
    position: absolute; left: 301px; top: 17px;
    font-family: Arial, sans-serif; font-size: 8.5px; line-height: 13px; color: #222;
  }
  .return-address strong { font-weight: 700; }
  .indicia {
    position: absolute; left: 490px; top: 26px; width: 51px; height: 50px;
    border: 1px solid #333; text-align: center;
    font-family: Arial, sans-serif; font-size: 6px; line-height: 8px; color: #222;
    padding-top: 3px;
  }
  .indicia .paid { font-size: 8.5px; line-height: 10px; }
  .recipient {
    position: absolute; left: 441px; top: 90px; width: 100px; height: 51px;
    border: 1px solid #333; padding: 14px 0 0 11px;
    font-family: Arial, sans-serif; font-size: 8.5px; line-height: 11px; color: #222;
  }
  .address-line { position: absolute; left: 318px; width: 220px; height: 1.5px; background: #333; }
</style>
</head>
<body>

<section class="card card--front">
  <div class="headline-band">
    <h1 class="headline">Healthy and happy pigs<br>because of a quality<br>job done</h1>
  </div>
  <div class="rule rule--light front-rule-light"></div>
  <div class="rule rule--dark front-rule-dark"></div>
  <p class="service">We clean and disinfect Hog confinements<br>in-order to receive new pigs</p>
  <p class="brand">Brandt and Daughters</p>
  <p class="web">www.brandtanddaughters-wash.com</p>
</section>

<section class="card card--back">
  <div class="barn-photo" role="img" aria-label="Photo of a long hog confinement barn with grain silos under a blue sky"></div>
  <div class="info-panel"></div>
  <div class="photo-band"></div>
  <div class="rule rule--light back-rule-light"></div>
  <div class="rule rule--dark back-rule-dark"></div>

  <p class="insured">WE ARE INSURED</p>
  <ul class="benefits">
    <li><svg viewBox="0 0 15 15"><rect x="1" y="3" width="10" height="10" fill="none" stroke="#555" stroke-width="1.4"/><path d="M3.5 8 L6.5 11 L13.5 2" fill="none" stroke="#8b3f48" stroke-width="2.2"/></svg>Clean Healthy barns</li>
    <li><svg viewBox="0 0 15 15"><rect x="1" y="3" width="10" height="10" fill="none" stroke="#555" stroke-width="1.4"/><path d="M3.5 8 L6.5 11 L13.5 2" fill="none" stroke="#8b3f48" stroke-width="2.2"/></svg>Work done in timely manner</li>
    <li><svg viewBox="0 0 15 15"><rect x="1" y="3" width="10" height="10" fill="none" stroke="#555" stroke-width="1.4"/><path d="M3.5 8 L6.5 11 L13.5 2" fill="none" stroke="#8b3f48" stroke-width="2.2"/></svg>100% satisfied</li>
    <li><svg viewBox="0 0 15 15"><rect x="1" y="3" width="10" height="10" fill="none" stroke="#555" stroke-width="1.4"/><path d="M3.5 8 L6.5 11 L13.5 2" fill="none" stroke="#8b3f48" stroke-width="2.2"/></svg>Bio-security</li>
    <li><svg viewBox="0 0 15 15"><rect x="1" y="3" width="10" height="10" fill="none" stroke="#555" stroke-width="1.4"/><path d="M3.5 8 L6.5 11 L13.5 2" fill="none" stroke="#8b3f48" stroke-width="2.2"/></svg>Water conservation</li>
  </ul>

  <address class="return-address" style="font-style:normal">
    <strong>Return Address</strong><br>
    Brandt &amp; Daughters<br>
    Street Name, City Name<br>
    State Zip Code
  </address>

  <div class="indicia">PRSRT STD<br>ECRWSS<br>U.S.POSTAGE<br><span class="paid">PAID</span><br>EDDM Retail</div>

  <div class="recipient">Local<br>Postal Customer</div>

  <div class="address-line" style="top:203px"></div>
  <div class="address-line" style="top:231px"></div>
  <div class="address-line" style="top:259px"></div>
  <div class="address-line" style="top:288px"></div>
</section>

</body>
</html>
```